Brovanek Data Yellow rose letterhead

I have a new logo for my company but in its current form it is too large to be used on letterhead or as a email signature. I need to have the designer use elements from the current logo and create something close to the original but more suited for smaller items.
Updates

I just uploaded a copy of our logo that does not have the weathered affect. Thanks

Reason: More time for revisions

Industry/Entity Type

It Company

Requirements
Must have
• The design must maintain the visual effect of the current logo. It needs to include the yellow rose and the name of the company.
Nice to have
• It would be nice to maintain the stamp theme and incorporate my name, address, phone, email. etc.

```html
<!DOCTYPE html>
<html lang="en">
<head>
<meta charset="utf-8">
<title>Brovanek Data Letterhead</title>
<link rel="stylesheet" href="https://fonts.googleapis.com/css2?family=Andika:wght@400;700&display=swap">
<style>
  :root {
    --ink: #5a4a42;
    --rule: #5b4c44;
    --stamp: #f39a3c;
    --paper: #ffffff;
  }
  html, body {
    margin: 0;
    padding: 0;
    overflow: hidden;
    background: var(--paper);
  }
  .letterhead {
    position: relative;
    width: 925px;
    height: 1200px;
    background: var(--paper);
    font-family: "Andika", sans-serif;
    color: var(--ink);
    overflow: hidden;
  }
  .brand {
    position: absolute;
    left: 212px;
    top: 58px;
    display: flex;
    align-items: center;
    gap: 16px;
  }
  .brand-mark {
    width: 60px;
    height: 60px;
    background: var(--stamp);
  }
  .brand-name {
    font-size: 34px;
    font-weight: 700;
    line-height: 1.05;
    color: var(--ink);
  }
  .sender {
    position: absolute;
    left: 462px;
    top: 62px;
    margin: 0;
    font-style: normal;
    font-size: 20px;
    font-weight: 700;
    line-height: 29px;
  }
  .header-rule {
    position: absolute;
    left: 56px;
    top: 210px;
    width: 810px;
    height: 6px;
    background: var(--rule);
  }
  .footer {
    position: absolute;
    left: 60px;
    right: 59px;
    top: 1148px;
    display: flex;
    align-items: center;
    gap: 18px;
  }
  .footer-rule {
    flex: 1;
    height: 5px;
    background: var(--rule);
  }
  .footer-email {
    font-size: 17px;
    font-weight: 700;
    color: var(--ink);
  }
</style>
</head>
<body>
  <div class="letterhead">
    <header>
      <div class="brand">
        <div class="brand-mark"></div>
        <div class="brand-name">Brovanek<br>Data</div>
      </div>
      <address class="sender">
        Mara Delacourt, PhD<br>
        218 Cedar Hollow Road, Ste 410<br>
        Marble Falls, TX 78654<br>
        1-800-555-0147
      </address>
      <div class="header-rule"></div>
    </header>
    <footer class="footer">
      <span class="footer-rule"></span>
      <span class="footer-email">mara@brovanek-data.com</span>
      <span class="footer-rule"></span>
    </footer>
  </div>
</body>
</html>
```